Awesome photographers card for an awesome new business

Double sided business card Black background and silver logo in middle on one side. Details on otherside. please keep it simple

Industry/Entity Type

Photographer

Contact Information for Business Card

Gerald Fenwick
0452817360
GeraldFenwickPhotography47@mailbox.test
www.GeraldFenwickPhotography.test.au
Instagram _Gerald_fenwick

Requirements
Must have
• My logo in Silver
• please use instagram logo instead of "Instagram"

```html
<!DOCTYPE html>
<html lang="en">
<head>
<meta charset="utf-8">
<title>Gerald Fenwick Photography — Business Card</title>
<link href="https://fonts.googleapis.com/css2?family=Montserrat:wght@400;500&display=swap" rel="stylesheet">
<style>
  :root {
    --backdrop: #141414;
    --card: #1b1b1b;
    --card-edge: #262626;
    --silver: #d9d9d9;
    --text: #f2f2f2;
  }
  html, body {
    margin: 0;
    padding: 0;
    width: 1200px;
    height: 900px;
    overflow: hidden;
    background: var(--backdrop);
    font-family: "Montserrat", sans-serif;
  }
  .canvas {
    width: 1200px;
    height: 900px;
    display: flex;
    flex-direction: column;
    align-items: center;
    justify-content: center;
    gap: 40px;
  }
  .card {
    position: relative;
    width: 700px;
    height: 400px;
    background: var(--card);
    border: 1px solid var(--card-edge);
    box-sizing: border-box;
    display: flex;
    align-items: center;
    justify-content: center;
  }
  /* Front side: name mark */
  .brand {
    display: flex;
    align-items: center;
    gap: 22px;
  }
  .brand__dot {
    width: 46px;
    height: 46px;
    border: 3px solid var(--silver);
    border-radius: 50%;
    box-sizing: border-box;
  }
  .brand__name {
    color: var(--silver);
    font-weight: 500;
    font-size: 26px;
    letter-spacing: 0.3em;
    text-transform: uppercase;
    line-height: 1.5;
  }
  /* Back side: details within ring */
  .details-ring {
    position: absolute;
    left: 50%;
    top: 50%;
    width: 376px;
    height: 376px;
    transform: translate(-50%, -50%);
  }
  .details {
    position: relative;
    text-align: center;
    color: var(--text);
    font-weight: 400;
  }
  .details__name {
    font-weight: 500;
    font-size: 16px;
    letter-spacing: 0.2em;
    text-transform: uppercase;
    margin: 0 0 14px;
  }
  .details__line {
    font-size: 14px;
    margin: 0 0 6px;
    letter-spacing: 0.01em;
  }
  .details__line--social {
    display: flex;
    align-items: center;
    justify-content: center;
    gap: 8px;
  }
  .social-mark {
    width: 12px;
    height: 12px;
    border: 1.5px solid var(--text);
    box-sizing: border-box;
  }
</style>
</head>
<body>
<main class="canvas">
  <section class="card card--front" aria-label="Card front">
    <div class="brand">
      <span class="brand__dot" aria-hidden="true"></span>
      <span class="brand__name">Gerald Fenwick<br>Photography</span>
    </div>
  </section>

  <section class="card card--back" aria-label="Card back">
    <svg class="details-ring" viewBox="0 0 376 376" aria-hidden="true">
      <circle cx="188" cy="188" r="184" fill="none" stroke="var(--silver)" stroke-width="4"/>
    </svg>
    <div class="details">
      <p class="details__name">Gerald Fenwick</p>
      <p class="details__line">0452817360</p>
      <p class="details__line details__line--social"><span class="social-mark" aria-hidden="true"></span>_Gerald_fenwick</p>
      <p class="details__line">www.GeraldFenwickPhotography.test.au</p>
      <p class="details__line">GeraldFenwickPhotography47@mailbox.test</p>
    </div>
  </section>
</main>
</body>
</html>
```